Business Card Design

WE are looking for a premium quality Business Cards for a Law Firm . Copies of our current business card is attached.

Contact Information for Business Card

xyz

```html
<!DOCTYPE html>
<html lang="en">
<head>
<meta charset="utf-8">
<title>Harcourt Lawyers – Business Cards</title>
<link href="https://fonts.googleapis.com/css2?family=Cinzel:wght@700&family=Arimo:wght@400&display=swap" rel="stylesheet">
<style>
  :root {
    --backdrop: #b1b2b4;
    --card: #ffffff;
    --green: #22503f;
    --ink-green: #163a2c;
    --gold: #c59a5b;
    --gold-text: #b8934e;
    --text: #3a3a3a;
    --rule: #7a7a7a;
  }
  * { margin: 0; padding: 0; box-sizing: border-box; }
  html, body { width: 1200px; height: 993px; overflow: hidden; background: var(--backdrop); }
  .sheet { position: relative; width: 1200px; height: 993px; }

  .card {
    position: absolute; width: 489px; height: 282px;
    background: var(--card);
    box-shadow: 0 1px 3px rgba(0,0,0,0.25);
    overflow: hidden;
    font-family: "Arimo", Arial, sans-serif;
    color: var(--text);
  }
  .card--a { left: 78px;  top: 207px; }
  .card--b { left: 629px; top: 207px; }
  .card--c { left: 75px;  top: 579px; }
  .card--d { left: 645px; top: 579px; }

  .brand { position: absolute; left: 293px; top: 29px; width: 160px; text-align: center; }
  .brand__ring { display: block; width: 56px; height: 56px; margin: 0 auto 6px; }
  .brand__name {
    font-family: "Cinzel", Georgia, serif; font-weight: 700; color: var(--ink-green);
    font-size: 23px; line-height: 24px; letter-spacing: 0.5px;
  }
  .brand__sub {
    font-family: "Cinzel", Georgia, serif; font-weight: 700; color: var(--ink-green);
    font-size: 9px; letter-spacing: 6.5px; line-height: 12px; margin-top: 1px; padding-left: 6px;
  }

  .person { position: absolute; left: 40px; top: 132px; }
  .person__name {
    font-family: "Cinzel", Georgia, serif; font-weight: 700; color: var(--ink-green);
    font-size: 18px; line-height: 20px; letter-spacing: 0.3px;
  }
  .person__role { color: var(--gold-text); font-size: 10.5px; line-height: 13px; margin-top: 1px; }

  .rule { position: absolute; left: 40px; width: 401px; height: 1px; background: var(--rule); top: 187px; }
  .card--b .rule { top: 172px; }

  .contacts { position: absolute; left: 40px; top: 193px; font-size: 11.5px; line-height: 14.6px; }
  .contacts li { list-style: none; display: flex; align-items: center; gap: 6px; }
  .contacts svg { width: 10px; height: 10px; flex: none; fill: var(--ink-green); }

  .address { position: absolute; top: 193px; font-size: 11.5px; line-height: 14.6px; }
  .address--right { right: 48px; text-align: right; }
  .address--left { left: 40px; }

  .band { position: absolute; left: 0; bottom: 0; width: 489px; height: 33px; }
  .website {
    position: absolute; right: 46px; bottom: 14px;
    font-size: 11.5px; color: #1e1e1e; letter-spacing: 0.1px;
  }
</style>
</head>
<body>
<main class="sheet">

  <!-- Card: principal, Brisbane office -->
  <article class="card card--a">
    <div class="brand">
      <svg class="brand__ring" viewBox="0 0 56 56"><circle cx="28" cy="28" r="26" fill="none" stroke="var(--gold)" stroke-width="2.6"/></svg>
      <div class="brand__name">HARCOURT</div>
      <div class="brand__sub">LAWYERS</div>
    </div>
    <div class="person">
      <h2 class="person__name">MARCUS DELANEY</h2>
      <p class="person__role">Principal Solicitor<br>MBA, Juris Doctor</p>
    </div>
    <div class="rule"></div>
    <ul class="contacts">
      <li><svg viewBox="0 0 10 10"><path d="M2 0.5l1.6 2.2-0.9 1.1c0.6 1.3 1.3 2 2.5 2.6l1.1-0.9 2.2 1.6-0.8 1.8C4.2 9 1 5.8 0.3 1.3z"/></svg>+61 7 3000 1234</li>
      <li><svg viewBox="0 0 10 10"><path d="M2.5 0h5v10h-5z M3.5 1v7h3V1z"/></svg>+61 0400 123 456</li>
      <li><svg viewBox="0 0 10 10"><path d="M0 2h10v6H0z" /><path d="M0 2l5 3.3L10 2" fill="none" stroke="#fff" stroke-width="0.8"/></svg>marcus@harcourtlawyers.com.au</li>
    </ul>
    <address class="address address--right" style="font-style:normal">Level 3, Harcourt House<br>88 Ridgeway Terrace<br>Kelvin Hill, QLD 4000</address>
    <svg class="band" viewBox="0 0 489 33"><polygon points="0,10 245,10 222,33 0,33" fill="var(--green)"/><polygon points="263,0 489,0 489,33 232,33" fill="var(--gold)"/></svg>
    <span class="website">www.harcourtlawyers.com.au</span>
  </article>

  <!-- Card: solicitor, both offices -->
  <article class="card card--b">
    <div class="brand">
      <svg class="brand__ring" viewBox="0 0 56 56"><circle cx="28" cy="28" r="26" fill="none" stroke="var(--gold)" stroke-width="2.6"/></svg>
      <div class="brand__name">HARCOURT</div>
      <div class="brand__sub">LAWYERS</div>
    </div>
    <div class="person">
      <h2 class="person__name">ELENA WHITFORD</h2>
      <p class="person__role">Solicitor</p>
    </div>
    <div class="rule"></div>
    <address class="address address--left" style="font-style:normal">Level 3, Harcourt House<br>88 Ridgeway Terrace<br>Kelvin Hill, QLD 4000</address>
    <address class="address address--right" style="font-style:normal">Suite 410, Beaumont Chambers<br>212 Ashby Lane<br>MELBOURNE VIC 3000</address>
    <svg class="band" viewBox="0 0 489 33"><polygon points="0,10 245,10 222,33 0,33" fill="var(--green)"/><polygon points="263,0 489,0 489,33 232,33" fill="var(--gold)"/></svg>
    <span class="website">www.harcourtlawyers.com.au</span>
  </article>

  <!-- Card: solicitor, Melbourne office -->
  <article class="card card--c">
    <div class="brand">
      <svg class="brand__ring" viewBox="0 0 56 56"><circle cx="28" cy="28" r="26" fill="none" stroke="var(--gold)" stroke-width="2.6"/></svg>
      <div class="brand__name">HARCOURT</div>
      <div class="brand__sub">LAWYERS</div>
    </div>
    <div class="person">
      <h2 class="person__name">DR PRIYA NANDAN</h2>
      <p class="person__role">Solicitor (Australia &amp; New Zealand)<br>BA.LL.B, LL.M, PhD</p>
    </div>
    <div class="rule"></div>
    <ul class="contacts">
      <li><svg viewBox="0 0 10 10"><path d="M2 0.5l1.6 2.2-0.9 1.1c0.6 1.3 1.3 2 2.5 2.6l1.1-0.9 2.2 1.6-0.8 1.8C4.2 9 1 5.8 0.3 1.3z"/></svg>+61 (3) 9000 5678</li>
      <li><svg viewBox="0 0 10 10"><path d="M2.5 0h5v10h-5z M3.5 1v7h3V1z"/></svg>+61 400 987 654</li>
      <li><svg viewBox="0 0 10 10"><path d="M0 2h10v6H0z" /><path d="M0 2l5 3.3L10 2" fill="none" stroke="#fff" stroke-width="0.8"/></svg>priya.nandan@harcourtlawyers.com.au</li>
    </ul>
    <address class="address address--right" style="font-style:normal">Suite 410, Beaumont Chambers<br>212 Ashby Lane<br>MELBOURNE VIC 3000</address>
    <svg class="band" viewBox="0 0 489 33"><polygon points="0,10 245,10 222,33 0,33" fill="var(--green)"/><polygon points="263,0 489,0 489,33 232,33" fill="var(--gold)"/></svg>
    <span class="website">www.harcourtlawyers.com.au</span>
  </article>

  <!-- Card: principal, Melbourne office -->
  <article class="card card--d">
    <div class="brand">
      <svg class="brand__ring" viewBox="0 0 56 56"><circle cx="28" cy="28" r="26" fill="none" stroke="var(--gold)" stroke-width="2.6"/></svg>
      <div class="brand__name">HARCOURT</div>
      <div class="brand__sub">LAWYERS</div>
    </div>
    <div class="person">
      <h2 class="person__name">MARCUS DELANEY</h2>
      <p class="person__role">Principal Solicitor<br>MBA, Juris Doctor</p>
    </div>
    <div class="rule"></div>
    <ul class="contacts">
      <li><svg viewBox="0 0 10 10"><path d="M2 0.5l1.6 2.2-0.9 1.1c0.6 1.3 1.3 2 2.5 2.6l1.1-0.9 2.2 1.6-0.8 1.8C4.2 9 1 5.8 0.3 1.3z"/></svg>+61 (3) 9000 5678</li>
      <li><svg viewBox="0 0 10 10"><path d="M2.5 0h5v10h-5z M3.5 1v7h3V1z"/></svg>+61 0400 123 456</li>
      <li><svg viewBox="0 0 10 10"><path d="M0 2h10v6H0z" /><path d="M0 2l5 3.3L10 2" fill="none" stroke="#fff" stroke-width="0.8"/></svg>marcus@harcourtlawyers.com.au</li>
    </ul>
    <address class="address address--right" style="font-style:normal">Suite 410, Beaumont Chambers<br>212 Ashby Lane<br>MELBOURNE VIC 3000</address>
    <svg class="band" viewBox="0 0 489 33"><polygon points="0,10 245,10 222,33 0,33" fill="var(--green)"/><polygon points="263,0 489,0 489,33 232,33" fill="var(--gold)"/></svg>
    <span class="website">www.harcourtlawyers.com.au</span>
  </article>

</main>
</body>
</html>
```